Brell Stone Company Business Cards

Front and Back Business Card - logo and text setup - cool design. I need workable photoshop or illustrator files so I can setup each employee card with design that is created
Updates

Hi everyone, thank you for the great entries. Please no more white and blue cards - there are so many already - black and silver only now please. thanks!

Target Market(s)

Construction Industry - Facility Managers

Industry/Entity Type

Construction

Contact Information for Business Card

I really like contemporary simplistic looks - clean neat....not opposed to seeing some black backrounds

Requirements
Must have
• Logo/website address with design on front only - www.brellstone-example.com (logo attached)
• Back:
• Name/Title/Company Address/Phone/email address
Nice to have
• Cool design
Should not have
• Nothing gimmicky like Fire or Water - since we are a Fire Protection company - it has all been done

```html
<!DOCTYPE html>
<html lang="en">
<head>
<meta charset="utf-8">
<title>Brell Stone Company Business Cards</title>
<link rel="stylesheet" href="https://fonts.googleapis.com/css2?family=Source+Sans+3:wght@400;600;700;900&display=swap">
<style>
  :root {
    --bg: #c9cdd1;
    --card-black: #000000;
    --brand-blue: #0323a0;
    --brand-red: #ff2222;
    --olive: #5f7a2e;
    --white: #ffffff;
  }
  * { margin: 0; padding: 0; box-sizing: border-box; }
  html, body {
    width: 1200px; height: 1193px; overflow: hidden;
    background: var(--bg);
    font-family: "Source Sans 3", Arial, sans-serif;
    color: var(--white);
  }
  .canvas { position: relative; width: 1200px; height: 1193px; }

  .card {
    position: absolute;
    width: 872px; height: 499px;
    border-radius: 25px;
    background: var(--card-black);
    overflow: hidden;
  }
  .card--front { left: 74px; top: 76px; }
  .card--back { left: 257px; top: 612px; }

  .wordmark {
    position: absolute;
    font-weight: 900;
    color: var(--brand-red);
    letter-spacing: -1px;
    line-height: 1;
    white-space: nowrap;
  }
  .card--front .wordmark { left: 52px; top: 58px; font-size: 84px; }
  .card--back .wordmark { left: 0; right: 0; top: 228px; text-align: center; font-size: 104px; }

  .address {
    position: absolute; left: 49px; top: 261px;
    font-size: 25px; font-weight: 400;
  }
  .divider {
    position: absolute; left: 0; right: 0; top: 310px;
    height: 5px; background: var(--olive);
  }
  .notch { position: absolute; left: 118px; top: 314px; }
  .info-band {
    position: absolute; left: 0; right: 0; top: 315px; bottom: 0;
    background: var(--brand-blue);
  }
  .notch { z-index: 2; }

  .person { position: absolute; left: 49px; top: 370px; }
  .person__name { font-size: 34px; font-weight: 700; line-height: 1.2; }
  .person__title { font-size: 31px; font-weight: 400; line-height: 1.2; }

  .contacts {
    position: absolute; right: 32px; top: 352px;
    list-style: none;
  }
  .contacts li {
    display: flex; align-items: center; justify-content: flex-end;
    gap: 14px; height: 38.5px;
    font-size: 22px;
  }
  .contacts svg { width: 24px; height: 24px; flex: none; }

  .back-url {
    position: absolute; left: 0; right: 0; top: 322px;
    text-align: center;
    font-size: 28px; letter-spacing: 6px;
  }
</style>
</head>
<body>
<div class="canvas">

  <section class="card card--front">
    <div class="wordmark">Brell Stone</div>
    <p class="address">48 Harbor Point Road, Millbrook, NY 11890</p>
    <div class="divider"></div>
    <div class="info-band"></div>
    <svg class="notch" width="40" height="20" viewBox="0 0 40 20">
      <polygon points="0,0 40,0 20,18" fill="var(--olive)" stroke="#000" stroke-width="2"/>
    </svg>
    <div class="person">
      <p class="person__name">Dana Whitfield</p>
      <p class="person__title">President</p>
    </div>
    <ul class="contacts">
      <li>(555) 014-2870
        <svg viewBox="0 0 24 24"><path d="M5 3l4 0 2 5-2.5 1.8a11 11 0 0 0 5.7 5.7L16 13l5 2v4a2 2 0 0 1-2 2A17 17 0 0 1 3 5a2 2 0 0 1 2-2z" fill="none" stroke="#fff" stroke-width="2" stroke-linejoin="round"/></svg>
      </li>
      <li>info@brellstone-example.com
        <svg viewBox="0 0 24 24"><rect x="2" y="5" width="20" height="14" fill="#fff"/><path d="M2 5l10 8 10-8M2 19l7.5-7M22 19l-7.5-7" fill="none" stroke="var(--brand-blue)" stroke-width="1.8"/></svg>
      </li>
      <li>www.brellstone-example.com
        <svg viewBox="0 0 24 24" fill="none" stroke="#fff" stroke-width="1.6"><circle cx="12" cy="12" r="10"/><ellipse cx="12" cy="12" rx="4.5" ry="10"/><path d="M2 12h20M4 7h16M4 17h16M12 2v20"/></svg>
      </li>
    </ul>
  </section>

  <section class="card card--back">
    <div class="wordmark">Brell Stone</div>
    <p class="back-url">www.brellstone-example.com</p>
  </section>

</div>
</body>
</html>
```